design a construction company business card

Design business card around our logo. Card must have all the typical info: name, title, address, phone, email, business name, etc. Somewhere on the card I would like to see our motto "Grounded in trust... Driven by craftsmanship." Consider adding a splash of bright orange to the card to complement the blues and silvers/grays in the logo. We are open to metallic inks, textures, etc. We would like to see options on both light and dark backgrounds. The font in the logo is Euro Technic Extended Regular.

```html
<!DOCTYPE html>
<html lang="en">
<head>
<meta charset="utf-8">
<title>Halvorsen Contracting – Business Cards</title>
<link href="https://fonts.googleapis.com/css2?family=Open+Sans:ital,wght@0,400;0,600;1,400&display=swap" rel="stylesheet">
<style>
  :root{
    --backdrop:#3a302b;
    --card:#1b1d20;
    --card-edge:#25282c;
    --silver:#b9bcc0;
    --white:#f2f3f5;
    --blue:#2f55c8;
    --blue-light:#4d74e0;
    --divider:#8a8f96;
  }
  *{box-sizing:border-box;margin:0;padding:0}
  html,body{width:1200px;height:864px;overflow:hidden}
  body{
    background:var(--backdrop);
    font-family:"Open Sans",Arial,sans-serif;
    position:relative;
  }
  .card{
    position:absolute;
    width:540px;height:308px;
    background:var(--card);
    border:1px solid var(--card-edge);
    border-radius:3px;
    box-shadow:0 10px 24px rgba(0,0,0,.35);
  }
  .card--back{left:50px;top:70px}
  .card--front{left:610px;top:486px}

  /* back */
  .card--back .wordmark{
    position:absolute;left:0;right:0;top:100px;
    text-align:center;
  }
  .wordmark__name{
    font-weight:600;font-size:30px;letter-spacing:4px;
    text-transform:uppercase;line-height:1;
    display:inline-flex;align-items:center;gap:12px;
  }
  .wordmark__mark{width:14px;height:14px;display:inline-block}
  .wordmark__sub{
    font-weight:600;font-size:12px;letter-spacing:5px;
    text-transform:uppercase;margin-top:8px;
  }
  .card--back .wordmark__name,
  .card--back .wordmark__sub{color:var(--silver)}
  .card--back .wordmark__mark{background:var(--silver)}
  .motto{
    position:absolute;left:0;right:0;top:200px;
    text-align:center;color:var(--white);
    font-style:italic;font-size:14px;letter-spacing:.3px;
  }

  /* front */
  .card--front .wordmark{
    position:absolute;left:26px;top:112px;width:250px;text-align:center;
  }
  .card--front .wordmark__name{font-size:22px;letter-spacing:3px;color:var(--blue-light)}
  .card--front .wordmark__mark{background:var(--blue-light);width:11px;height:11px}
  .card--front .wordmark__sub{font-size:10px;letter-spacing:4px;color:var(--blue-light)}
  .divider{
    position:absolute;left:296px;top:62px;width:1px;height:184px;
    background:var(--divider);
  }
  .contact{position:absolute;left:318px;top:70px;color:var(--white)}
  .contact__name{color:var(--blue);font-weight:600;font-size:17px;letter-spacing:.5px;text-transform:uppercase;line-height:1.1}
  .contact__title{font-size:13px;text-transform:uppercase;letter-spacing:.5px;margin-bottom:10px}
  .contact__address{font-size:13px;line-height:1.35;margin-bottom:8px}
  .contact__list{list-style:none;font-size:13px;line-height:1.6}
  .contact__list li{display:flex;align-items:center;gap:8px}
  .icon{width:13px;height:13px;flex:none}
</style>
</head>
<body>

  <section class="card card--back" aria-label="Business card, back">
    <div class="wordmark">
      <div class="wordmark__name"><span class="wordmark__mark"></span>Halvorsen</div>
      <div class="wordmark__sub">Contracting, Inc.</div>
    </div>
    <p class="motto">Grounded in trust... Driven by craftsmanship.</p>
  </section>

  <section class="card card--front" aria-label="Business card, front">
    <div class="wordmark">
      <div class="wordmark__name"><span class="wordmark__mark"></span>Halvorsen</div>
      <div class="wordmark__sub">Contracting, Inc.</div>
    </div>
    <div class="divider"></div>
    <div class="contact">
      <p class="contact__name">Mark Ellison</p>
      <p class="contact__title">President</p>
      <p class="contact__address">2417 Harborview Lane<br>Millbrook, NY 12545</p>
      <ul class="contact__list">
        <li>
          <svg class="icon" viewBox="0 0 16 16" aria-hidden="true"><circle cx="8" cy="8" r="8" fill="#2f55c8"/><path d="M5 4.5l1.6-.4.9 2-1 .8a6 6 0 002.6 2.6l.8-1 2 .9-.4 1.6c-3.6.2-6.7-2.9-6.5-6.5z" fill="#f2f3f5"/></svg>
          555 0142 7781
        </li>
        <li>
          <svg class="icon" viewBox="0 0 16 16" aria-hidden="true"><circle cx="8" cy="8" r="8" fill="#2f55c8"/><rect x="4" y="5" width="8" height="6" fill="#f2f3f5"/><path d="M4 5l4 3.2L12 5" fill="none" stroke="#2f55c8" stroke-width="1"/></svg>
          mark@halvorsen.com
        </li>
        <li>
          <svg class="icon" viewBox="0 0 16 16" aria-hidden="true"><circle cx="8" cy="8" r="8" fill="#2f55c8"/><circle cx="8" cy="8" r="4" fill="none" stroke="#f2f3f5" stroke-width="1"/><path d="M4 8h8M8 4c-1.6 2.2-1.6 5.8 0 8M8 4c1.6 2.2 1.6 5.8 0 8" fill="none" stroke="#f2f3f5" stroke-width="0.9"/></svg>
          www.halvorsen.com
        </li>
      </ul>
    </div>
  </section>

</body>
</html>
```